Website Redesign Brief for Breezeline Climate Services WA

Creating a clear and concise brief for designers to redesign your website, https://breezelineclimatewa.com.au/, is essential to ensure the project aligns with your vision for a more energetic, friendly, optimistic, and user-friendly website. Below is a sample brief tailored to your request, balancing specificity with flexibility to allow designers to bring their creativity to the table.

Website Redesign Brief for Breezeline Climate WA
1. Project Overview

We are seeking a redesign of our website, https://breezelineclimatewa.com.au/, to create a vibrant, engaging, and user-friendly online presence that reflects our brand’s commitment to providing top-notch air conditioning services in Western Australia. The redesigned website should feel energetic, friendly, and optimistic while maintaining professionalism and improving user experience.
2. Goals and Objectives

Enhance Brand Perception: Convey a modern, approachable, and positive brand identity that resonates with both residential and commercial clients.
Improve User Experience: Simplify navigation, improve accessibility, and ensure a seamless experience across devices (desktop, tablet, mobile).
Increase Engagement: Encourage visitors to explore services, request quotes, and contact us through clear calls-to-action (CTAs).
Boost Conversion Rates: Make it easier for users to find information and take action (e.g., booking services or inquiries).
Showcase Expertise: Highlight our professional air conditioning services, experience, and customer satisfaction in an inviting way.

3. Target Audience

Primary Audience: Homeowners and small business owners in Western Australia seeking air conditioning installation, maintenance, or repair services.
Secondary Audience: Property managers, commercial clients, and real estate professionals looking for reliable HVAC solutions.
Demographics: Ages 25–65, mix of tech-savvy and non-tech-savvy users, located primarily in Perth and surrounding areas.
User Needs: Clear information about services, transparent pricing, easy contact options, and reassurance of quality and reliability.

4. Design Preferences

Tone and Style:

Energetic: Use bold, vibrant colors (e.g., blues, whites, and pops of warm tones like orange or yellow) to evoke energy and optimism.
Friendly: Incorporate approachable language, welcoming imagery, and a clean, uncluttered layout.
Optimistic: Highlight positive customer outcomes (e.g., comfort, energy savings) through visuals and messaging.
Professional yet approachable: Maintain credibility as a trusted service provider while avoiding a cold or overly corporate feel.

Visual Elements:

Use high-quality images of happy customers, comfortable homes/offices, and modern air conditioning units.
Incorporate subtle animations or micro-interactions to add energy (e.g., hover effects on buttons or smooth scrolling).
Avoid overly complex graphics that may slow down the site or distract from usability.

Typography: Clean, modern fonts that are easy to read. Use larger, bold headings for hierarchy and warmth.
Inspiration: Websites like https://www.vorlex.com.au/ (clean and professional) or https://www.tandoraclimatech.com.au/ (user-friendly and modern) but with a more vibrant and welcoming vibe.

5. Functional Requirements

User-Friendly Navigation: Simplify the menu structure to make key pages (e.g., Services, About Us, Contact) easily accessible.
Mobile Responsiveness: Ensure the site is fully optimized for mobile devices, with fast load times and intuitive touch interactions.
Key Features:

Prominent CTAs for requesting quotes, booking services, or contacting the team.
A clear service overview with icons or visuals for each service (e.g., installation, repairs, maintenance).
A testimonials section to showcase customer satisfaction.
An easy-to-use contact form with minimal fields.
Integration with Google Maps for location-based services or office directions.

SEO and Performance: Optimize for search engines (e.g., keywords like “air conditioning Perth”) and ensure fast loading speeds.
Accessibility: Follow WCAG guidelines to ensure the site is usable for all visitors, including those with disabilities.

6. Content Guidance

Existing Content: Review and refine current content from https://breezelineclimatewa.com.au/ to make it concise, engaging, and aligned with the friendly tone.
New Content Ideas:

Add a “Why Choose Us” section highlighting expertise, customer service, and eco-friendly solutions.
Include a FAQ page to address common customer questions.
Create a blog section for tips on air conditioning maintenance or energy efficiency (optional).

Tone of Voice: Conversational, reassuring, and positive. Avoid technical jargon unless clearly explained.

7. Technical Considerations

Platform: Open to recommendations (e.g., WordPress, Wix, or custom-built) but prioritize ease of maintenance and scalability.
Integrations: Ensure compatibility with existing tools (e.g., Google Analytics, CRM for quote requests, or booking systems).
Domain and Hosting: Retain current domain (breezelineclimatewa.com.au); hosting recommendations welcome.
Timeline: Initial design concepts within [insert timeline, e.g., 2–3 weeks], with full redesign completed by [insert deadline, e.g., 6–8 weeks].
Budget: [Insert budget range or state “flexible, please provide a quote”].

8. Deliverables

Wireframes and mockups for homepage, service pages, and contact page.
Fully responsive website design with all necessary pages.
Style guide (colors, fonts, imagery guidelines).
CMS setup (if applicable) with basic training for content updates.
Testing and optimization for performance and SEO.

9. Success Metrics

Increased time on site and reduced bounce rate.
Higher conversion rates for quote requests and contact form submissions.
Positive user feedback on ease of navigation and overall experience.
Improved search engine rankings for key terms within [insert timeframe, e.g., 3 months].

10. Additional Notes

Please provide a portfolio of similar projects or examples of user-friendly, vibrant websites.
We are open to creative suggestions to make the website stand out in the HVAC industry.
Regular progress updates and collaboration during the design process are appreciated.
Updates

designers are asking for more time

few have requested an extension. I Have extended

Target Market(s)

Primary Audience: Homeowners and small business owners in Western Australia seeking air conditioning installation, maintenance, or repair services. Secondary Audience: Property managers, commercial clients, and real estate professionals looking for reliable HVAC solutions. Demographics: Ages 25–65, mix of tech-savvy and non-tech-savvy users, located primarily in Perth and surrounding areas. User Needs: Clear information about services, transparent pricing, easy contact options, and reassurance of quality and reliability.

Industry/Entity Type

Air Conditioning and Refrigeration (HVAC & R)

Coding

Coded - Design and coding required

Colors
0054AA
0677BA
7BADD7
CADEEF
E8F1F8
59FF00
82FF00
B8FF75
E3FFCB
F4FFEA
F0912C
F2A743
F7CA91
FBE8D2
FDF5EE
EE7325
F08F49
F5BC92
FAE3D3
FDF4ED

Requirements
Must have
• Must have all my current information I currently have on my web page.
Nice to have
• A sales page for people to buy products online

```html
<!DOCTYPE html>
<html lang="en">
<head>
<meta charset="utf-8">
<title>Breezeline Climate Services WA</title>
<link rel="stylesheet" href="https://fonts.googleapis.com/css2?family=Michroma&family=Lexend:wght@300;400;500;600;700&display=swap">
<style>
:root{
  --orange:#EE7325;
  --orange-2:#F0842D;
  --orange-deep:#E05A1C;
  --gold:#F2A743;
  --navy:#23397A;
  --navy-2:#2E4C9A;
  --ink:#1d1d1f;
  --text:#555a62;
  --white:#ffffff;
  --line:#e6e6e6;
  --footer:#1e1e20;
  --star:#F2A743;
}
*{margin:0;padding:0;box-sizing:border-box}
html,body{width:1200px;height:5333px;overflow:hidden;background:var(--white)}
body{font-family:'Lexend',sans-serif;color:var(--ink)}
.page{position:relative;width:1200px;height:5333px;overflow:hidden}
.abs{position:absolute}
.display{font-family:'Michroma',sans-serif;text-transform:uppercase;letter-spacing:.5px}
.eyebrow{font-weight:500;font-size:17px;text-transform:uppercase;color:var(--orange);letter-spacing:.3px}
.center{left:0;width:1200px;text-align:center}
.btn{display:flex;align-items:center;justify-content:center;border-radius:22px;font-weight:500;font-size:14px;text-transform:uppercase;color:var(--white)}
.btn-orange{background:var(--orange)}
.btn-navy{background:var(--navy)}
.divider{width:70px;height:4px;border-radius:2px;background:var(--orange)}
.divider.on-orange{background:#fff}
.divider.on-navy{background:var(--gold)}

/* header */
.topbar-quote{left:668px;top:0;width:234px;height:40px;background:var(--orange);color:#fff;font-size:14px;font-weight:600;display:flex;align-items:center;justify-content:center;clip-path:polygon(0 0,100% 0,96% 100%,4% 100%)}
.topbar-contact{left:894px;top:0;width:306px;height:40px;background:var(--navy);color:#fff;font-size:14px;font-weight:600;display:flex;align-items:center;justify-content:center;clip-path:polygon(3% 0,100% 0,100% 100%,0 100%)}
.header{left:0;top:0;width:1200px;height:120px;background:var(--white)}
.brand{left:93px;top:18px;width:200px;display:flex;flex-direction:column;align-items:center;gap:8px}
.brand-dot{width:46px;height:46px;border-radius:50%;background:var(--orange)}
.brand-name{font-weight:600;color:var(--navy);font-size:14px;text-align:center;line-height:1.2}
.nav{left:346px;top:68px;display:flex;gap:30px;font-size:13.5px;text-transform:uppercase;color:#333}
.nav .active{color:var(--orange);position:relative}
.nav .active::after{content:"";position:absolute;left:0;right:0;bottom:-10px;height:2px;background:var(--orange)}

/* hero */
.hero{left:0;top:120px;width:1200px;height:580px}
.hero-title{top:236px;font-size:33px;color:var(--gold)}
.hero-sub{top:288px;font-size:22px;color:#fff}
.hero-text{left:230px;top:334px;width:740px;text-align:center;font-size:14.5px;line-height:1.65;color:#fff}

/* about */
.about-title{left:120px;top:828px;font-size:29px}
.about-text{left:120px;top:926px;width:388px;font-size:12.5px;line-height:2.1;color:var(--text);text-align:justify}
.play{left:798px;top:942px;width:80px;height:80px;border-radius:50%;background:var(--orange);display:flex;align-items:center;justify-content:center}

/* services */
.services-title{top:1330px;font-size:28px;color:#fff}
.service-card{top:1444px;width:305px;height:180px;border:2px solid rgba(255,255,255,.85);border-radius:6px;display:flex;flex-direction:column;align-items:center;justify-content:flex-end;padding:0 14px 16px;color:#fff;font-size:16.5px;font-weight:500;text-align:center;line-height:1.5}
.service-card.is-active{background:var(--navy);border-color:var(--navy)}
.service-icon{position:absolute;top:18px;left:50%;transform:translateX(-50%);width:84px;height:84px;border-radius:50%;background:#fff;display:flex;align-items:center;justify-content:center}
.service-icon.dark{background:#151515}
.arrow-circle{width:32px;height:32px;border-radius:50%;border:2px solid #fff;display:flex;align-items:center;justify-content:center}
.detail-title{left:627px;top:1700px;font-size:21px;color:#fff;line-height:1.45;font-weight:500}
.detail-list{left:627px;top:1776px;list-style:none;color:#fff;font-size:16.5px}
.detail-list li{height:25.7px;display:flex;align-items:center;gap:10px}

/* why */
.why-title{top:2332px;font-size:27px}
.feature-h{font-weight:600;font-size:19px;line-height:1.5}
.feature-p{font-size:13px;line-height:2;color:var(--text)}
.feature-left{width:280px;text-align:right}
.feature-right{width:240px;text-align:left}
.feature-icon{width:96px;height:96px;border-radius:50%;display:flex;align-items:center;justify-content:center;box-shadow:0 0 0 7px #fff,0 4px 16px rgba(0,0,0,.18)}
.feature-icon.orange{background:var(--orange)}
.feature-icon.navy{background:var(--navy)}
.hub{left:445px;top:2499px;width:310px;height:310px;border-radius:50%;background:#fff;box-shadow:0 6px 26px rgba(0,0,0,.16);display:flex;align-items:center;justify-content:center}
.hub-inner{width:262px;height:262px;border-radius:50%;border:2px solid var(--orange);display:flex;flex-direction:column;align-items:center;justify-content:center;gap:12px}

/* brands */
.brands-title{top:2985px;font-size:28px}
.brand-box{top:3097px;width:224px;height:106px;background:#fff;box-shadow:0 4px 14px rgba(0,0,0,.14);display:flex;align-items:center;justify-content:center;gap:10px;font-weight:600;font-size:18px}

/* blog */
.blog-title{top:3398px;font-size:29px;color:#fff}
.post{top:3517px;width:292px;color:#fff}
.post-img{width:292px;height:286px}
.post-title{margin:22px 10px 0;font-size:19px;font-weight:600;line-height:1.45}
.post-text{margin:10px 10px 0;font-size:12.5px;line-height:2;color:#dfe5f3}
.post-date{margin:6px 10px 0;font-size:13px;font-weight:600;display:flex;align-items:center;gap:8px}
.arrow-white{border-color:#fff}

/* testimonials */
.testi-title{top:4196px;font-size:30px}
.testi{top:4308px;width:303px;height:296px;background:#fff;box-shadow:0 4px 18px rgba(0,0,0,.13);padding:22px 24px}
.testi-head{display:flex;gap:18px;align-items:flex-start}
.quote-mark{width:94px;height:94px;border-radius:50%;background:var(--orange);flex:none;display:flex;align-items:center;justify-content:center;box-shadow:0 0 0 5px #fde3d3}
.testi-name{color:var(--navy);font-weight:600;font-size:17px;margin-top:8px}
.testi-date{font-size:13px;color:var(--text);margin-top:6px}
.stars{color:var(--star);font-size:14px;letter-spacing:2px;margin-top:6px}
.testi-text{margin-top:24px;font-size:13px;line-height:2;color:var(--text);text-align:justify}
.arrow-dark{border-color:#333}

/* footer */
.footer-h{font-weight:600;font-size:16px;color:#fff;text-transform:uppercase}
.quick-links{list-style:none;color:#dcdcdc;font-size:14px}
.quick-links li{height:32px;display:flex;align-items:center;gap:10px}
.contact-item{display:flex;gap:12px;color:#dcdcdc;font-size:13.5px;line-height:1.85}
.contact-item strong{color:#fff;font-weight:600}
.contact-pin{width:26px;height:26px;border-radius:50%;background:var(--orange);flex:none;display:flex;align-items:center;justify-content:center;margin-top:4px}
.social{width:32px;height:32px;border-radius:50%;background:var(--orange)}
.copyright{top:5284px;font-size:13.5px;color:#dcdcdc}
</style>
</head>
<body>
<div class="page">

  <!-- HERO -->
  <section class="abs hero" aria-label="Hero">
    <svg width="1200" height="580" viewBox="0 0 1200 580" class="abs" style="left:0;top:0">
      <defs>
        <linearGradient id="heroBg" x1="0" y1="0" x2="1" y2="1">
          <stop offset="0" stop-color="#3c4356"/>
          <stop offset=".55" stop-color="#6b5a4c"/>
          <stop offset="1" stop-color="#8a6a52"/>
        </linearGradient>
      </defs>
      <rect width="1200" height="580" fill="url(#heroBg)" role="img" aria-label="Photo of a couple relaxing on a sofa in a cool living room"/>
      <rect width="1200" height="580" fill="#1c2035" opacity=".35"/>
      <path d="M0 430 Q560 700 1200 400 L1200 445 Q560 740 0 470Z" fill="var(--navy)"/>
      <path d="M0 470 Q560 740 1200 445 L1200 580 L0 580Z" fill="var(--orange)"/>
      <path d="M0 505 Q560 760 1200 480 L1200 580 L0 580Z" fill="#ffffff"/>
    </svg>
  </section>

  <header class="abs header"></header>
  <div class="abs topbar-quote">REQUEST A QUOTE</div>
  <div class="abs topbar-contact">CONTACT US</div>
  <div class="abs brand">
    <span class="brand-dot"></span>
    <span class="brand-name">Breezeline Climate<br>Services WA</span>
  </div>
  <nav class="abs nav">
    <span class="active">Home</span><span>About Us</span><span>Services</span><span>Cleaning</span><span>Regasing</span><span>Commissioning</span><span>Air Balancing</span>
  </nav>

  <p class="abs center" style="top:202px;color:#fff;font-size:14px;font-weight:500">QUALITY SERVICES</p>
  <h1 class="abs center display hero-title">Quality Air Conditioning</h1>
  <h2 class="abs center display hero-sub">Repairs, Service, and Installations</h2>
  <p class="abs hero-text">Our service is second to none; we have a team of experienced technicians that consistently deliver the best quality air conditioner repairs Perth has to offer. There are many different brands of air conditioning on the market, each with their own way of controlling the temperature of your home.</p>
  <div class="abs btn btn-orange" style="left:490px;top:430px;width:218px;height:40px">Book a Service</div>

  <!-- ABOUT -->
  <p class="abs eyebrow" style="left:120px;top:797px">About Us</p>
  <h2 class="abs display about-title">Need a Technician?</h2>
  <div class="abs divider" style="left:120px;top:890px"></div>
  <p class="abs about-text">Our call out fee includes the first half hour on site. In most cases will be able to diagnose the problem with in that time, and repair it if no parts are required. If any parts, gas or additional labour is required, we will let you know before we proceed</p>
  <div class="abs btn btn-orange" style="left:120px;top:1086px;width:215px;height:42px">More About Us</div>
  <div class="abs" style="left:645px;top:790px;width:417px;height:346px;background:var(--orange);border-radius:18px"></div>
  <div class="abs" role="img" aria-label="Photo of a technician servicing a wall-mounted air conditioner" style="left:627px;top:808px;width:417px;height:328px;border-radius:18px;background:linear-gradient(135deg,#c9ccd1,#7d858f 55%,#4a4f58)"></div>
  <div class="abs play"><svg width="30" height="30" viewBox="0 0 30 30"><path d="M9 5 L25 15 L9 25Z" fill="#fff"/></svg></div>

  <!-- SERVICES -->
  <svg class="abs" style="left:0;top:1200px" width="1200" height="1000" viewBox="0 0 1200 1000">
    <defs>
      <linearGradient id="svcBg" x1="0" y1="0" x2="1" y2="1">
        <stop offset="0" stop-color="var(--orange-deep)"/>
        <stop offset="1" stop-color="var(--orange-2)"/>
      </linearGradient>
    </defs>
    <path d="M0 124 Q600 -84 1200 124 L1200 869 Q600 1117 0 869Z" fill="url(#svcBg)"/>
  </svg>
  <p class="abs center" style="top:1295px;color:#fff;font-size:17px;font-weight:500">SOME OF OUR SPECIALITY</p>
  <h2 class="abs center display services-title">Our Services</h2>
  <div class="abs divider on-orange" style="left:565px;top:1395px"></div>

  <div class="abs arrow-circle" style="left:50px;top:1513px"><svg width="14" height="14" viewBox="0 0 14 14"><path d="M12 7H2M6 3L2 7l4 4" stroke="#fff" stroke-width="1.8" fill="none"/></svg></div>
  <div class="abs arrow-circle" style="left:1112px;top:1513px"><svg width="14" height="14" viewBox="0 0 14 14"><path d="M2 7h10M8 3l4 4-4 4" stroke="#fff" stroke-width="1.8" fill="none"/></svg></div>

  <div class="abs service-card is-active" style="left:120px">
    <span class="service-icon"><svg width="44" height="44" viewBox="0 0 44 44" fill="none" stroke="var(--navy)" stroke-width="2.2"><circle cx="22" cy="18" r="11"/><rect x="7" y="30" width="30" height="8" rx="2"/><path d="M17 13l10 10M27 13L17 23"/></svg></span>
    Commercial Air Conditioning Installation &amp; Repairs
  </div>
  <div class="abs service-card" style="left:447px">
    <span class="service-icon dark"><svg width="44" height="44" viewBox="0 0 44 44" fill="none" stroke="#fff" stroke-width="2.2"><rect x="6" y="10" width="32" height="14" rx="3"/><path d="M12 20h20M14 28v8M22 28v10M30 28v8"/></svg></span>
    Domestic aircon installation &amp; repairs
  </div>
  <div class="abs service-card" style="left:776px">
    <span class="service-icon dark"><svg width="44" height="44" viewBox="0 0 44 44" fill="none" stroke="#fff" stroke-width="2.2"><rect x="8" y="8" width="28" height="28" rx="4"/><circle cx="22" cy="22" r="8"/><path d="M22 14v16M14 22h16"/></svg></span>
    Coolroom installation &amp; repairs
  </div>

  <div class="abs" style="left:134px;top:1686px;width:435px;height:348px;background:var(--navy);border-radius:20px"></div>
  <div class="abs" role="img" aria-label="Photo of a technician working on a commercial condenser unit" style="left:150px;top:1694px;width:419px;height:340px;border-radius:20px;background:linear-gradient(140deg,#e7eaee,#a9b0b8 50%,#5d6570)"></div>

  <h3 class="abs detail-title">Commercial Air Conditioning<br>Installation &amp; Repairs</h3>
  <ul class="abs detail-list">
    <li><svg width="16" height="14" viewBox="0 0 16 14"><path d="M1 1l6 6-6 6M8 1l6 6-6 6" stroke="#fff" stroke-width="2.2" fill="none"/></svg>Refrigerant leak</li>
    <li><svg width="16" height="14" viewBox="0 0 16 14"><path d="M1 1l6 6-6 6M8 1l6 6-6 6" stroke="#fff" stroke-width="2.2" fill="none"/></svg>Commercial designing</li>
    <li><svg width="16" height="14" viewBox="0 0 16 14"><path d="M1 1l6 6-6 6M8 1l6 6-6 6" stroke="#fff" stroke-width="2.2" fill="none"/></svg>Airflow optimisation</li>
    <li><svg width="16" height="14" viewBox="0 0 16 14"><path d="M1 1l6 6-6 6M8 1l6 6-6 6" stroke="#fff" stroke-width="2.2" fill="none"/></svg>Commercial Installation</li>
    <li><svg width="16" height="14" viewBox="0 0 16 14"><path d="M1 1l6 6-6 6M8 1l6 6-6 6" stroke="#fff" stroke-width="2.2" fill="none"/></svg>Chiller service &amp; repair</li>
    <li><svg width="16" height="14" viewBox="0 0 16 14"><path d="M1 1l6 6-6 6M8 1l6 6-6 6" stroke="#fff" stroke-width="2.2" fill="none"/></svg>Frozen evaporator coil</li>
    <li><svg width="16" height="14" viewBox="0 0 16 14"><path d="M1 1l6 6-6 6M8 1l6 6-6 6" stroke="#fff" stroke-width="2.2" fill="none"/></svg>Faulty fan motor</li>
    <li><svg width="16" height="14" viewBox="0 0 16 14"><path d="M1 1l6 6-6 6M8 1l6 6-6 6" stroke="#fff" stroke-width="2.2" fill="none"/></svg>No power</li>
    <li><svg width="16" height="14" viewBox="0 0 16 14"><path d="M1 1l6 6-6 6M8 1l6 6-6 6" stroke="#fff" stroke-width="2.2" fill="none"/></svg>Faulty compressor</li>
    <li><svg width="16" height="14" viewBox="0 0 16 14"><path d="M1 1l6 6-6 6M8 1l6 6-6 6" stroke="#fff" stroke-width="2.2" fill="none"/></svg>Clogged condenser coils</li>
  </ul>
  <div class="abs btn btn-navy" style="left:490px;top:2090px;width:218px;height:41px">Book a Service</div>

  <!-- WHY CHOOSE US -->
  <p class="abs center eyebrow" style="top:2300px">Why Choose Us?</p>
  <h2 class="abs center display why-title">Experience. Reliability. Quality</h2>
  <div class="abs divider" style="left:565px;top:2398px"></div>

  <svg class="abs" style="left:0;top:2450px" width="1200" height="420" viewBox="0 0 1200 420" fill="none" stroke="#555" stroke-width="1.5" stroke-dasharray="5 4">
    <path d="M420 64 Q470 64 500 82"/>
    <path d="M786 60 Q730 60 700 82"/>
    <path d="M420 353 Q470 353 500 330"/>
    <path d="M782 353 Q730 353 700 330"/>
  </svg>

  <div class="abs hub"><div class="hub-inner"><span class="brand-dot" style="width:54px;height:54px"></span><span class="brand-name" style="font-size:16px">Breezeline Climate<br>Services WA</span></div></div>

  <div class="abs feature-left" style="left:20px;top:2448px">
    <h3 class="feature-h">Trusted Expertise</h3>
    <p class="feature-p" style="margin-top:8px">Our licensed technicians have extensive experience with all major air conditioning and refrigeration systems.</p>
  </div>
  <div class="abs feature-icon orange" style="left:324px;top:2466px"><svg width="44" height="44" viewBox="0 0 44 44" fill="none" stroke="#fff" stroke-width="2"><circle cx="22" cy="16" r="6"/><path d="M10 36c2-8 22-8 24 0M22 4l2 3h3l-2 2 1 3-4-2-4 2 1-3-2-2h3z"/></svg></div>

  <div class="abs feature-icon navy" style="left:786px;top:2462px"><svg width="44" height="44" viewBox="0 0 44 44" fill="none" stroke="#fff" stroke-width="2"><circle cx="22" cy="24" r="13"/><path d="M22 24l6-6M19 7h6M22 7v4"/></svg></div>
  <div class="abs feature-right" style="left:900px;top:2450px">
    <h3 class="feature-h">Fast Response Times</h3>
    <p class="feature-p" style="margin-top:8px">Whether it's an urgent repair or routine service, we act quickly to get your system back up and running.</p>
  </div>

  <div class="abs feature-left" style="left:20px;top:2744px">
    <h3 class="feature-h">Upfront &amp; Honest<br>Pricing</h3>
    <p class="feature-p" style="margin-top:8px">No surprises. We explain costs clearly before any work begins.</p>
  </div>
  <div class="abs feature-icon navy" style="left:324px;top:2755px"><svg width="44" height="44" viewBox="0 0 44 44" fill="none" stroke="#fff" stroke-width="2"><path d="M8 38V24h8v14M16 26c6-2 10-8 12-14 2 0 4 2 3 6h6c2 0 3 2 2 4l-3 10c-1 2-2 2-4 2H16"/></svg></div>

  <div class="abs feature-icon orange" style="left:782px;top:2755px"><svg width="44" height="44" viewBox="0 0 44 44" fill="none" stroke="#fff" stroke-width="2"><path d="M22 6a11 11 0 0 0-6 20v5h12v-5a11 11 0 0 0-6-20zM17 36h10M19 40h6"/></svg></div>
  <div class="abs feature-right" style="left:900px;top:2753px">
    <h3 class="feature-h">Complete Solutions</h3>
    <p class="feature-p" style="margin-top:8px">From domestic and commercial aircon to chillers, coolrooms, and BMS upgrades — we do it all.</p>
  </div>

  <!-- BRANDS -->
  <p class="abs center eyebrow" style="top:2952px">Brands</p>
  <h2 class="abs center display brands-title">Our Recommended Brands</h2>
  <div class="abs divider" style="left:565px;top:3050px"></div>
  <div class="abs brand-box" style="left:120px"><span style="width:14px;height:14px;background:var(--orange)"></span><span style="color:var(--ink)">Tandora Climatech</span></div>
  <div class="abs brand-box" style="left:364px"><span style="color:var(--navy-2)">Coolmere Systems</span></div>
  <div class="abs brand-box" style="left:608px"><span style="color:var(--navy)">Vorlex</span></div>
  <div class="abs brand-box" style="left:852px"><span style="width:14px;height:14px;border-radius:50%;background:var(--navy)"></span><span style="color:var(--navy)">Ventaro</span></div>

  <!-- BLOG -->
  <svg class="abs" style="left:0;top:3280px" width="1200" height="830" viewBox="0 0 1200 830">
    <defs>
      <linearGradient id="blogBg" x1="0" y1="0" x2="1" y2="0">
        <stop offset="0" stop-color="#1f3374"/>
        <stop offset="1" stop-color="#2c4a98"/>
      </linearGradient>
    </defs>
    <path d="M0 135 Q600 -115 1200 135 L1200 690 Q600 940 0 690Z" fill="url(#blogBg)"/>
  </svg>
  <p class="abs center" style="top:3364px;color:#fff;font-size:17px;font-weight:500">OUR BLOG</p>
  <h2 class="abs center display blog-title">Tips, Insights &amp; Expert Advice</h2>
  <div class="abs divider on-navy" style="left:565px;top:3460px"></div>

  <div class="abs arrow-circle arrow-white" style="left:77px;top:3683px"><svg width="14" height="14" viewBox="0 0 14 14"><path d="M12 7H2M6 3L2 7l4 4" stroke="#fff" stroke-width="1.8" fill="none"/></svg></div>
  <div class="abs arrow-circle arrow-white" style="left:1091px;top:3683px"><svg width="14" height="14" viewBox="0 0 14 14"><path d="M2 7h10M8 3l4 4-4 4" stroke="#fff" stroke-width="1.8" fill="none"/></svg></div>

  <article class="abs post" style="left:145px">
    <div class="post-img" role="img" aria-label="Photo of rooftop condenser units at sunset" style="background:linear-gradient(180deg,#2d3c5c,#c2733b 55%,#1c2230)"></div>
    <h3 class="post-title">Lorem Ipsum is simply dummy</h3>
    <p class="post-text">Lorem Ipsum is simply dummy text of the printing and typesetting industry.</p>
    <p class="post-date"><svg width="18" height="18" viewBox="0 0 18 18" fill="none" stroke="#fff" stroke-width="1.6"><circle cx="9" cy="9" r="7.5"/><path d="M9 4.5V9l3 2"/></svg>August 9,2025</p>
  </article>
  <article class="abs post" style="left:455px">
    <div class="post-img" role="img" aria-label="Photo of a ceiling cassette air conditioner among ductwork" style="background:linear-gradient(180deg,#b7c2cc,#5e6d7c 60%,#2b3644)"></div>
    <h3 class="post-title">Lorem Ipsum is simply dummy</h3>
    <p class="post-text">Lorem Ipsum is simply dummy text of the printing and typesetting industry.</p>
    <p class="post-date"><svg width="18" height="18" viewBox="0 0 18 18" fill="none" stroke="#fff" stroke-width="1.6"><circle cx="9" cy="9" r="7.5"/><path d="M9 4.5V9l3 2"/></svg>August 9,2025</p>
  </article>
  <article class="abs post" style="left:766px">
    <div class="post-img" role="img" aria-label="Photo of a technician repairing a rooftop unit in front of a city skyline" style="background:linear-gradient(180deg,#5c7690,#344a62 55%,#c1532a)"></div>
    <h3 class="post-title">Lorem Ipsum is simply dummy</h3>
    <p class="post-text">Lorem Ipsum is simply dummy text of the printing and typesetting industry.</p>
    <p class="post-date"><svg width="18" height="18" viewBox="0 0 18 18" fill="none" stroke="#fff" stroke-width="1.6"><circle cx="9" cy="9" r="7.5"/><path d="M9 4.5V9l3 2"/></svg>August 9,2025</p>
  </article>

  <!-- TESTIMONIALS -->
  <p class="abs center eyebrow" style="top:4163px">Testimonial</p>
  <h2 class="abs center display testi-title">Customer Feedback</h2>
  <div class="abs divider" style="left:565px;top:4260px"></div>

  <div class="abs arrow-circle arrow-dark" style="left:42px;top:4436px"><svg width="14" height="14" viewBox="0 0 14 14"><path d="M12 7H2M6 3L2 7l4 4" stroke="#333" stroke-width="1.8" fill="none"/></svg></div>
  <div class="abs arrow-circle arrow-dark" style="left:1103px;top:4436px"><svg width="14" height="14" viewBox="0 0 14 14"><path d="M2 7h10M8 3l4 4-4 4" stroke="#333" stroke-width="1.8" fill="none"/></svg></div>

  <article class="abs testi" style="left:114px">
    <div class="testi-head">
      <span class="quote-mark"><svg width="40" height="30" viewBox="0 0 40 30" fill="#fff"><path d="M2 14a12 12 0 0 1 12-12v6a6 6 0 0 0-6 6h6v14H2zM22 14a12 12 0 0 1 12-12v6a6 6 0 0 0-6 6h6v14H22z"/></svg></span>
      <div><p class="testi-name">Daniel Pryor K</p><p class="testi-date">4 days ago</p><p class="stars">★★★★★</p></div>
    </div>
    <p class="testi-text">Thank you Marcus and Theo for installing our 18kW Vorlex. My brother, who's a fridgy tech, checked the install and said it's near perfect. Couldn't be happier.</p>
  </article>
  <article class="abs testi" style="left:441px">
    <div class="testi-head">
      <span class="quote-mark"><svg width="40" height="30" viewBox="0 0 40 30" fill="#fff"><path d="M2 14a12 12 0 0 1 12-12v6a6 6 0 0 0-6 6h6v14H2zM22 14a12 12 0 0 1 12-12v6a6 6 0 0 0-6 6h6v14H22z"/></svg></span>
      <div><p class="testi-name">Rowan</p><p class="testi-date">7/26/2025</p><p class="stars">★★★★★</p></div>
    </div>
    <p class="testi-text">Marcus, thank you for fixing my mums aircon and helping us with the insurance claim. Above and beyond. I appreciate it.</p>
  </article>
  <article class="abs testi" style="left:768px">
    <div class="testi-head">
      <span class="quote-mark"><svg width="40" height="30" viewBox="0 0 40 30" fill="#fff"><path d="M2 14a12 12 0 0 1 12-12v6a6 6 0 0 0-6 6h6v14H2zM22 14a12 12 0 0 1 12-12v6a6 6 0 0 0-6 6h6v14H22z"/></svg></span>
      <div><p class="testi-name">Hollis</p><p class="testi-date">7/26/2025</p><p class="stars">★★★★★</p></div>
    </div>
    <p class="testi-text">Please thank Marcus for his professionalism and honesty. He advised us that a service was not required after checking over everything and fixed other items.</p>
  </article>

  <!-- FOOTER -->
  <svg class="abs" style="left:0;top:4680px" width="1200" height="653" viewBox="0 0 1200 653">
    <path d="M0 150 Q620 110 1200 10 L1200 653 L0 653Z" fill="var(--footer)"/>
    <path d="M0 118 Q620 80 1200 -20 L1200 10 Q620 110 0 150Z" fill="var(--orange)"/>
    <path d="M120 90 Q640 60 1200 -40 L1200 -20 Q640 82 120 108Z" fill="var(--navy)"/>
  </svg>

  <div class="abs" style="left:118px;top:4900px;width:186px;display:flex;flex-direction:column;align-items:center;gap:10px">
    <span class="brand-dot"></span>
    <span class="brand-name" style="color:#fff">Breezeline Climate<br>Services WA</span>
    <div style="display:flex;gap:16px;margin-top:10px"><span class="social"></span><span class="social"></span><span class="social"></span></div>
  </div>

  <h4 class="abs footer-h" style="left:341px;top:4872px">Quick Links</h4>
  <ul class="abs quick-links" style="left:341px;top:4906px">
    <li><svg width="14" height="12" viewBox="0 0 14 12"><path d="M1 6h11M8 2l4 4-4 4" stroke="#fff" stroke-width="1.8" fill="none"/></svg>Home</li>
    <li><svg width="14" height="12" viewBox="0 0 14 12"><path d="M1 6h11M8 2l4 4-4 4" stroke="#fff" stroke-width="1.8" fill="none"/></svg>About</li>
    <li><svg width="14" height="12" viewBox="0 0 14 12"><path d="M1 6h11M8 2l4 4-4 4" stroke="#fff" stroke-width="1.8" fill="none"/></svg>Service</li>
    <li><svg width="14" height="12" viewBox="0 0 14 12"><path d="M1 6h11M8 2l4 4-4 4" stroke="#fff" stroke-width="1.8" fill="none"/></svg>Project Works</li>
    <li><svg width="14" height="12" viewBox="0 0 14 12"><path d="M1 6h11M8 2l4 4-4 4" stroke="#fff" stroke-width="1.8" fill="none"/></svg>Residential Services</li>
    <li><svg width="14" height="12" viewBox="0 0 14 12"><path d="M1 6h11M8 2l4 4-4 4" stroke="#fff" stroke-width="1.8" fill="none"/></svg>Careers</li>
    <li><svg width="14" height="12" viewBox="0 0 14 12"><path d="M1 6h11M8 2l4 4-4 4" stroke="#fff" stroke-width="1.8" fill="none"/></svg>Contact</li>
  </ul>

  <h4 class="abs footer-h" style="left:542px;top:4872px">Contact Us</h4>
  <div class="abs contact-item" style="left:542px;top:4912px;width:280px">
    <span class="contact-pin"><svg width="12" height="14" viewBox="0 0 12 14"><path d="M6 13s5-5 5-8A5 5 0 0 0 1 5c0 3 5 8 5 8z" fill="#fff"/></svg></span>
    <div><strong>Location</strong><br>27 Banksia Vale Road,<br>Harrisdale WA 6112</div>
  </div>
  <div class="abs contact-item" style="left:542px;top:5000px;width:280px">
    <span class="contact-pin"><svg width="12" height="12" viewBox="0 0 12 12"><path d="M2 1l2 0 1 3-1.5 1a7 7 0 0 0 3.5 3.5L8 7l3 1v2c0 1-1 1-1 1A9 9 0 0 1 1 2c0 0 0-1 1-1z" fill="#fff"/></svg></span>
    <div><strong>Have Any Question</strong><br>0400 555 018</div>
  </div>
  <div class="abs contact-item" style="left:542px;top:5064px;width:300px">
    <span class="contact-pin"><svg width="13" height="10" viewBox="0 0 13 10"><rect x=".5" y=".5" width="12" height="9" fill="#fff"/><path d="M1 1l5.5 4.5L12 1" stroke="var(--orange)" fill="none"/></svg></span>
    <div><strong>Send your mail at</strong><br>info@breezelineclimatewa.com.au</div>
  </div>
  <div class="abs contact-item" style="left:542px;top:5128px;width:300px">
    <span class="contact-pin"><svg width="13" height="13" viewBox="0 0 13 13" fill="none" stroke="#fff" stroke-width="1.6"><circle cx="6.5" cy="6.5" r="5.5"/><path d="M6.5 3.5v3l2 1.5"/></svg></span>
    <div><strong>Working Hours</strong><br>Mon-Fri: 8.00am to 5.00pm<br>Weekends and Public Holidays:<br>Additional Callout Fee.</div>
  </div>

  <h4 class="abs footer-h" style="left:863px;top:4872px">Our Location</h4>
  <div class="abs" role="img" aria-label="Map showing the office location" style="left:858px;top:4918px;width:216px;height:195px;background:linear-gradient(135deg,#e9efe6,#d6e4d2 60%,#cfd8dd)"></div>

  <div class="abs" style="left:120px;top:5257px;width:960px;height:1px;background:#4a4a4e"></div>
  <p class="abs center copyright">© Copyright 2025 Breezeline Climate Services WA. All Rights Reserved</p>

</div>
</body>
</html>
```